Business card for event manager / organizer "waiter service"

Draft of a new valuable business card for my company.
Events, personnel service providers, festivals

```html
<!DOCTYPE html>
<html lang="de">
<head>
<meta charset="utf-8">
<title>Jonas Feldmann – Kellnerservice</title>
<link rel="stylesheet" href="https://fonts.googleapis.com/css2?family=Jura:wght@400;500&display=swap">
<style>
  :root {
    --orange: #f0821e;
    --dark: #1b1a1b;
    --shadow: rgba(0, 0, 0, 0.85);
  }
  html, body {
    margin: 0;
    padding: 0;
    width: 1200px;
    height: 720px;
    overflow: hidden;
    background: var(--dark);
  }
  .card {
    position: relative;
    width: 1200px;
    height: 720px;
    background: var(--dark);
    font-family: "Jura", sans-serif;
    color: var(--orange);
  }
  .card__shapes {
    position: absolute;
    inset: 0;
  }
  .identity {
    position: absolute;
    left: 48px;
    width: 487px;
    top: 325px;
    text-align: center;
  }
  .identity__name {
    margin: 0;
    font-size: 50px;
    font-weight: 500;
    line-height: 1;
    letter-spacing: 0.5px;
  }
  .identity__role {
    margin: 14px 0 0;
    font-size: 23px;
    font-weight: 500;
    letter-spacing: 4px;
  }
  .contacts {
    position: absolute;
    left: 566px;
    top: 0;
    margin: 0;
    padding: 0;
    list-style: none;
  }
  .contact {
    position: absolute;
    left: 0;
    display: flex;
    align-items: center;
    white-space: nowrap;
    transform: translateY(-50%);
  }
  .contact__icon {
    width: 40px;
    height: 40px;
    flex: none;
    margin-right: 22px;
    fill: none;
    stroke: var(--orange);
    stroke-width: 2.2;
    stroke-linecap: round;
    stroke-linejoin: round;
  }
  .contact__icon--solid { fill: var(--orange); stroke: none; }
  .contact__text { font-size: 30px; font-weight: 500; }
  .contact--phone .contact__text { font-size: 36px; letter-spacing: 0.5px; }
  .contact--phone-1 { top: 206px; }
  .contact--phone-2 { top: 264px; }
  .contact--web { top: 324px; }
  .contact--mail { top: 384px; }
  .contact--address { top: 450px; }
  .contact--social { top: 515px; }
</style>
</head>
<body>
<main class="card">
  <svg class="card__shapes" width="1200" height="720" viewBox="0 0 1200 720" aria-hidden="true">
    <defs>
      <filter id="hex-shadow" x="-20%" y="-20%" width="150%" height="150%">
        <feDropShadow dx="28" dy="14" stdDeviation="10" flood-color="#000" flood-opacity="0.85"/>
      </filter>
    </defs>
    <polygon class="accent-field" fill="var(--orange)" points="0,0 505,0 284,360 505,720 0,720"/>
    <polygon class="name-hexagon" fill="var(--dark)" filter="url(#hex-shadow)"
             points="291,79 535,218 535,500 291,640 48,500 48,218"/>
  </svg>

  <header class="identity">
    <h1 class="identity__name">Jonas Feldmann</h1>
    <p class="identity__role">Inhaber</p>
  </header>

  <ul class="contacts">
    <li class="contact contact--phone contact--phone-1">
      <svg class="contact__icon contact__icon--solid" viewBox="0 0 24 24"><path d="M6.6 10.8a15.1 15.1 0 0 0 6.6 6.6l2.2-2.2c.3-.3.7-.4 1-.2 1.1.4 2.3.6 3.6.6.6 0 1 .4 1 1V20c0 .6-.4 1-1 1A17 17 0 0 1 3 4c0-.6.4-1 1-1h3.5c.6 0 1 .4 1 1 0 1.3.2 2.5.6 3.6.1.3 0 .7-.2 1z"/></svg>
      <span class="contact__text">02364 512 73 48</span>
    </li>
    <li class="contact contact--phone contact--phone-2">
      <svg class="contact__icon contact__icon--solid" viewBox="0 0 24 24"><path d="M6.6 10.8a15.1 15.1 0 0 0 6.6 6.6l2.2-2.2c.3-.3.7-.4 1-.2 1.1.4 2.3.6 3.6.6.6 0 1 .4 1 1V20c0 .6-.4 1-1 1A17 17 0 0 1 3 4c0-.6.4-1 1-1h3.5c.6 0 1 .4 1 1 0 1.3.2 2.5.6 3.6.1.3 0 .7-.2 1z"/></svg>
      <span class="contact__text">0176 248 31 97</span>
    </li>
    <li class="contact contact--web">
      <svg class="contact__icon" viewBox="0 0 24 24"><circle cx="12" cy="12" r="9.5"/><ellipse cx="12" cy="12" rx="4.2" ry="9.5"/><path d="M2.5 12h19M4 7h16M4 17h16M12 2.5v19"/></svg>
      <span class="contact__text">www.jonas-kellnerservice.de</span>
    </li>
    <li class="contact contact--mail">
      <svg class="contact__icon" viewBox="0 0 24 24"><path d="M3 10l9 6 9-6v11H3z"/><path d="M3 21l7-6M21 21l-7-6"/><path d="M6 12V3h12v9"/><circle cx="12" cy="8" r="2"/><path d="M14 8v1a1.5 1.5 0 0 0 3 0V8a5 5 0 1 0-2 4"/></svg>
      <span class="contact__text">info.jonas-kellnerservice.de</span>
    </li>
    <li class="contact contact--address">
      <svg class="contact__icon" viewBox="0 0 24 24"><path d="M12 22s-7-7.6-7-13a7 7 0 0 1 14 0c0 5.4-7 13-7 13z"/><circle cx="12" cy="9" r="2.8"/></svg>
      <span class="contact__text">Birkenweg 5, 45721 Haltern</span>
    </li>
    <li class="contact contact--social">
      <svg class="contact__icon contact__icon--solid" viewBox="0 0 24 24"><circle cx="12" cy="12" r="10.5"/></svg>
      <span class="contact__text">www.socialnet.com/jonaskellnerservice</span>
    </li>
  </ul>
</main>
</body>
</html>
```